Velvet Lantern rebranding my business with a new business card

I have my new logo and now I need a refresher on my business cards. I really want something fun and fresh. I like black background or anything to make the color pop.
Logo
Name: Velvet Lantern
Contact Info as stated below:
Mira Pellow
555-013-4762
Logo
Name: Velvet Lantern
Mira Pellow
555-013-4762
fb.me/VelvetLanternbyMira
Instagram: @VelvetLanternbyMira

Industry/Entity Type

Business

Contact Information for Business Card

double-sided. Logo on one side. Contact info on the other.

Requirements
Must have
• Logo
• Name: Velvet Lantern
• Contact Info as stated below:
• Mira Pellow
• 555-013-4762
• fb.me/VelvetLanternbyMira
• fb.me/VelvetLanternbyMira

```html
<!DOCTYPE html>
<html lang="en">
<head>
<meta charset="utf-8">
<title>Velvet Lantern — Business Card</title>
<link href="https://fonts.googleapis.com/css2?family=Oswald:wght@500&family=Work+Sans:wght@400&display=swap" rel="stylesheet">
<style>
  :root {
    --backdrop: #e4e4e4;
    --card: #ffffff;
    --teal: #2bb5a0;
    --accent-red: #c8102e;
    --ink: #4a4a4a;
    --ink-dark: #222222;
    --blush: #f2a7c0;
    --blush-soft: #fbe3ec;
  }
  html, body {
    margin: 0;
    padding: 0;
    width: 1200px;
    height: 900px;
    overflow: hidden;
    background: var(--backdrop);
  }
  .sheet {
    position: relative;
    width: 1200px;
    height: 900px;
  }
  .card {
    position: absolute;
    left: 300px;
    width: 600px;
    height: 343px;
    background: var(--card);
    box-shadow: 0 6px 18px rgba(0,0,0,0.18);
  }
  .card--logo { top: 70px; }
  .card--contact { top: 487px; }

  .brand-mark {
    position: absolute;
    left: 50%;
    top: 50%;
    transform: translate(-50%, -50%);
    width: 170px;
    height: 170px;
    border-radius: 50%;
    border: 3px solid var(--blush);
    background: var(--blush-soft);
    display: flex;
    align-items: center;
    justify-content: center;
    text-align: center;
  }
  .brand-mark__name {
    font-family: "Work Sans", sans-serif;
    font-weight: 400;
    font-size: 22px;
    line-height: 1.2;
    color: var(--ink-dark);
  }

  .contact-block {
    position: absolute;
    left: 0;
    right: 0;
    top: 148px;
    display: flex;
    align-items: center;
    justify-content: center;
    gap: 18px;
    transform: translateX(20px);
  }
  .identity { text-align: right; }
  .identity__name {
    font-family: "Oswald", sans-serif;
    font-weight: 500;
    font-size: 34px;
    letter-spacing: 1px;
    line-height: 1;
    color: var(--teal);
    text-transform: uppercase;
  }
  .identity__role {
    font-family: "Work Sans", sans-serif;
    font-size: 15px;
    color: var(--ink-dark);
    margin-top: 4px;
  }
  .divider {
    width: 2px;
    height: 62px;
    background: var(--accent-red);
  }
  .contact-list {
    list-style: none;
    margin: 0;
    padding: 0;
    font-family: "Work Sans", sans-serif;
    font-size: 16px;
    color: var(--ink);
    line-height: 24px;
  }
  .contact-list li {
    display: flex;
    align-items: center;
    gap: 12px;
  }
  .contact-list svg { width: 14px; height: 14px; flex: none; }
</style>
</head>
<body>
<main class="sheet">
  <section class="card card--logo" aria-label="Card front">
    <div class="brand-mark">
      <span class="brand-mark__name">Velvet<br>Lantern</span>
    </div>
  </section>

  <section class="card card--contact" aria-label="Card back">
    <div class="contact-block">
      <div class="identity">
        <div class="identity__name">Mira Pellow</div>
        <div class="identity__role">Owner</div>
      </div>
      <div class="divider"></div>
      <ul class="contact-list">
        <li>
          <svg viewBox="0 0 14 14" aria-hidden="true"><rect x="3.5" y="1" width="7" height="12" rx="1.2" fill="none" stroke="var(--teal)" stroke-width="1.5"/></svg>
          555-013-4762
        </li>
        <li>
          <svg viewBox="0 0 14 14" aria-hidden="true"><rect x="1" y="3" width="12" height="8" fill="var(--teal)"/><path d="M1 3 L7 8 L13 3" fill="none" stroke="#fff" stroke-width="1.2"/></svg>
          info@mirapellow.com
        </li>
        <li>
          <svg viewBox="0 0 14 14" aria-hidden="true"><rect x="1.5" y="1.5" width="11" height="11" rx="1.5" fill="var(--teal)"/></svg>
          me/VelvetLanternbyMira
        </li>
      </ul>
    </div>
  </section>
</main>
</body>
</html>
```